Executive Business Card for Healthcare Company [Need Today]

I need a business card design for a healthcare company. The only branding the company has thus far is a logo. The cards will be utilized by company executives. The design I envision will be vibrant and appealing but with a corporate feel. They shouldn't be too casual or playful. I would like to complete this project TODAY if possible.

Target Market(s)

Healthcare vendors, other executives in healthcare and pharmaceuticals

Industry/Entity Type

Pharmaceutical

Contact Information for Business Card

See attachment

Font styles to use
Serif
Sans Serif

Colors

Designer to choose colors to be used in the design.

```html
<!DOCTYPE html>
<html lang="en">
<head>
<meta charset="utf-8">
<title>Corvane Therapeutics – Business Card</title>
<link href="https://fonts.googleapis.com/css2?family=Roboto:wght@300;400;500&display=swap" rel="stylesheet">
<style>
  :root {
    --backdrop: #3a3a3c;
    --card: #232325;
    --card-mark: #111113;
    --front-text: #4a4a4d;
    --muted: #d9d9db;
    --white: #ffffff;
    --teal: #22b4c8;
    --green: #3fbf8a;
    --stripe: #9a9a9e;
  }
  * { margin: 0; padding: 0; box-sizing: border-box; }
  html, body {
    width: 799px; height: 1200px; overflow: hidden;
    background: var(--backdrop);
    font-family: "Roboto", Arial, sans-serif;
  }
  .sheet {
    width: 799px; height: 1200px;
    display: flex; flex-direction: column; align-items: center; justify-content: space-around;
    padding: 60px 0;
  }
  .card {
    position: relative;
    width: 680px; height: 389px;
    background: var(--card);
    border-radius: 3px;
    box-shadow: 0 12px 30px rgba(0,0,0,.45);
    overflow: hidden;
  }

  /* Front */
  .front-brand {
    position: absolute; left: 60px; top: 100px;
    display: flex; align-items: center; gap: 26px;
  }
  .front-brand .mark {
    width: 120px; height: 120px; border-radius: 50%;
    border: 3px solid var(--card-mark);
  }
  .front-brand .name {
    font-size: 46px; font-weight: 300; line-height: 1.05;
    color: var(--front-text); letter-spacing: 1px;
  }
  .front-url {
    position: absolute; left: 60px; bottom: 50px;
    font-size: 20px; font-weight: 400; letter-spacing: 4px;
    color: var(--muted);
  }

  /* Back */
  .back-brand {
    position: absolute; left: 60px; top: 36px;
    width: 280px;
    display: flex; flex-direction: column; align-items: center; gap: 14px;
  }
  .back-brand .mark {
    width: 106px; height: 106px; border-radius: 50%;
    border: 5px solid var(--green);
  }
  .back-brand .name {
    font-size: 34px; font-weight: 300; line-height: 1.05;
    color: var(--teal); text-align: center;
  }
  .contact {
    position: absolute; left: 390px; top: 92px;
    color: var(--white);
  }
  .contact .person { font-size: 30px; font-weight: 500; color: var(--teal); }
  .contact .role { font-size: 15px; font-weight: 400; color: var(--muted); margin: 4px 0 14px; }
  .contact ul { list-style: none; }
  .contact li {
    display: flex; align-items: center; gap: 10px;
    font-size: 18px; line-height: 26px;
  }
  .contact li svg { width: 15px; height: 15px; flex: none; fill: var(--teal); }
  .contact .address { margin-top: 2px; font-size: 18px; line-height: 25px; }
  .bands { position: absolute; left: 0; top: 0; }
  .back-url {
    position: absolute; left: 350px; bottom: 22px;
    font-size: 20px; color: var(--white);
  }
</style>
</head>
<body>
<main class="sheet">

  <section class="card card-front">
    <div class="front-brand">
      <span class="mark"></span>
      <span class="name">Corvane<br>Therapeutics</span>
    </div>
    <p class="front-url">www.corvanerx.com</p>
  </section>

  <section class="card card-back">
    <svg class="bands" width="680" height="389" viewBox="0 0 680 389">
      <defs>
        <linearGradient id="bandFill" x1="0" x2="1" y1="0" y2="0">
          <stop offset="0" stop-color="#22b4c8"/>
          <stop offset="1" stop-color="#3fbf8a"/>
        </linearGradient>
      </defs>
      <polygon points="0,300 316,300 300,322 0,322" fill="#9a9a9e"/>
      <polygon points="316,300 680,300 680,389 252,389" fill="url(#bandFill)"/>
    </svg>

    <div class="back-brand">
      <span class="mark"></span>
      <span class="name">Corvane<br>Therapeutics</span>
    </div>

    <div class="contact">
      <p class="person">Daniel Harlow</p>
      <p class="role">Senior Director of Marketing</p>
      <ul>
        <li>
          <svg viewBox="0 0 16 16"><path d="M3 1h3l1.5 4-2 1.3a9 9 0 0 0 4.2 4.2L11 8.5l4 1.5v3a2 2 0 0 1-2 2A12 12 0 0 1 1 3a2 2 0 0 1 2-2z"/></svg>
          555-201-4470
        </li>
        <li>
          <svg viewBox="0 0 16 16"><path d="M4 0h8a1 1 0 0 1 1 1v14a1 1 0 0 1-1 1H4a1 1 0 0 1-1-1V1a1 1 0 0 1 1-1zm1 2v10h6V2zm3 11a1 1 0 1 0 0 2 1 1 0 0 0 0-2z"/></svg>
          555-318-2256
        </li>
        <li>
          <svg viewBox="0 0 16 16"><path d="M8 0a8 8 0 1 0 0 16A8 8 0 0 0 8 0zm0 1.5c.9 0 2 1.8 2.3 5H5.7C6 3.3 7.1 1.5 8 1.5zM1.6 7.5h2.6c0-1.8.3-3.5 1-4.7A6.5 6.5 0 0 0 1.6 7.5zm0 1h2.6c0 1.8.3 3.5 1 4.7a6.5 6.5 0 0 1-3.6-4.7zm4.1 0h4.6c-.3 3.2-1.4 5-2.300 5s-2-1.8-2.300-5zm6.1 0h2.6a6.5 6.5 0 0 1-3.6 4.7c.7-1.2 1-2.9 1-4.7zm2.6-1h-2.6c0-1.8-.3-3.5-1-4.7a6.5 6.5 0 0 1 3.6 4.7z"/></svg>
          dharlow@corvanerx.com
        </li>
      </ul>
      <p class="address">18 Linden Park Avenue<br>Fairview, GA 30000</p>
    </div>

    <p class="back-url">www.corvanerx.com</p>
  </section>

</main>
</body>
</html>
```